Freelance business trainer needs a new business card

My business is called Brontlearn. I provide training in the workplace on management, coaching and mentoring, and customer service topics for a variety of businesses, colleges and private training providers, and teach on management programs. I need a professional but eye catching business card. Business colours grey and orange. My name Marion Tadwick; Tel 07382 415067; email mtadwick@brontlearn.co.uk; website www.brontlearn.co.uk.
Happy to have some sort of logo on front and details on back or all on one side
Target Market(s)
SME businesses and colleges - workshops i run are for adults in the workplace
Industry/Entity Type
Training
Look and feel

```html
<!DOCTYPE html>
<html lang="en">
<head>
<meta charset="utf-8">
<title>Brontlearn — Business Card</title>
<link rel="stylesheet" href="https://fonts.googleapis.com/css2?family=Roboto+Condensed:wght@400;700&display=swap">
<style>
  :root {
    --page-bg: #e9e9ec;
    --card-white: #fbfbf8;
    --brand-grey: #6e7173;
    --brand-orange: #e2741a;
    --text-light: #ffffff;
    --logo-grey: #5f6264;
  }
  * { box-sizing: border-box; margin: 0; padding: 0; }
  html, body {
    width: 1200px;
    height: 800px;
    overflow: hidden;
    background: var(--page-bg);
  }
  .canvas {
    position: relative;
    width: 1200px;
    height: 800px;
  }
  .business-card {
    position: absolute;
    left: 160px;
    top: 130px;
    width: 880px;
    height: 540px;
    background: var(--card-white);
    overflow: hidden;
    box-shadow: 0 6px 22px rgba(0,0,0,0.18);
    font-family: "Roboto Condensed", "Arial Narrow", sans-serif;
  }
  .card-shapes {
    position: absolute;
    inset: 0;
    width: 100%;
    height: 100%;
  }
  .shape-grey { fill: var(--brand-grey); }
  .shape-orange { fill: var(--brand-orange); }

  .brand {
    position: absolute;
    left: 468px;
    top: 100px;
    display: flex;
    align-items: center;
    gap: 14px;
  }
  .brand-dot {
    width: 100px;
    height: 100px;
    border-radius: 50%;
    background: var(--brand-orange);
  }
  .brand-name {
    font-size: 58px;
    font-weight: 400;
    color: var(--logo-grey);
    letter-spacing: 0.5px;
  }

  .person {
    position: absolute;
    left: 42px;
    top: 262px;
  }
  .person-name {
    font-size: 31px;
    font-weight: 700;
    color: var(--brand-orange);
    letter-spacing: 0.8px;
  }
  .person-role {
    margin-top: 2px;
    font-size: 24px;
    color: var(--text-light);
    letter-spacing: 0.3px;
  }

  .contact-list {
    position: absolute;
    left: 56px;
    top: 372px;
    list-style: none;
  }
  .contact-item {
    display: flex;
    align-items: center;
    gap: 16px;
    height: 40px;
    font-size: 24px;
    color: var(--text-light);
    letter-spacing: 0.6px;
  }
  .contact-icon {
    width: 22px;
    height: 22px;
    flex: none;
    fill: var(--brand-orange);
  }
</style>
</head>
<body>
<main class="canvas">
  <section class="business-card" aria-label="Brontlearn business card">
    <svg class="card-shapes" viewBox="0 0 880 540" preserveAspectRatio="none" aria-hidden="true">
      <path class="shape-grey" d="M0,0 L86,0 C200,240 470,372 880,362 L880,540 L0,540 Z"/>
      <path class="shape-orange" d="M70,0 L76,0 C190,232 460,356 880,344 L880,326 C470,338 200,222 70,0 Z"/>
    </svg>

    <div class="brand">
      <span class="brand-dot"></span>
      <span class="brand-name">Brontlearn</span>
    </div>

    <div class="person">
      <p class="person-name">Marion Tadwick</p>
      <p class="person-role">Senior Education Consultant</p>
    </div>

    <ul class="contact-list">
      <li class="contact-item">
        <svg class="contact-icon" viewBox="0 0 24 24" aria-hidden="true">
          <path d="M3 7c0-2 2-3 9-3s9 1 9 3v2h-5V7H8v2H3z"/>
          <path d="M6 11h12l2 9H4z"/>
        </svg>
        <span>07382 415067</span>
      </li>
      <li class="contact-item">
        <svg class="contact-icon" viewBox="0 0 24 24" aria-hidden="true">
          <path d="M2 5h20v2l-10 7L2 7z"/>
          <path d="M2 9l10 7 10-7v10H2z"/>
        </svg>
        <span>mtadwick@brontlearn.co.uk</span>
      </li>
      <li class="contact-item">
        <svg class="contact-icon" viewBox="0 0 24 24" aria-hidden="true">
          <path fill-rule="evenodd" d="M12 2a10 10 0 1 1 0 20a10 10 0 1 1 0-20zM11 4.1C9.4 5.8 8.6 8 8.5 11H11zM13 4.1V11h2.5C15.4 8 14.6 5.8 13 4.1zM4.1 11h2.4c.1-2.6.7-4.7 1.8-6.2A8 8 0 0 0 4.1 11zM17.5 11h2.4a8 8 0 0 0-4.2-6.2c1.1 1.5 1.7 3.6 1.8 6.2zM4.1 13a8 8 0 0 0 4.2 6.2C7.2 17.7 6.6 15.6 6.5 13zM8.5 13c.1 3 .9 5.2 2.5 6.9V13zM13 13v6.9c1.6-1.7 2.4-3.9 2.5-6.9zM17.5 13c-.1 2.6-.7 4.7-1.8 6.2a8 8 0 0 0 4.2-6.2z"/>
        </svg>
        <span>www.brontlearn.co.uk.</span>
      </li>
    </ul>
  </section>
</main>
</body>
</html>
```